New business card for a regional office of a US M&A company

We need business card for a finance company, office based in Hong Kong , our Head office is in US, our business is to Merge and acquires companies , the new office will be a regional office for the Asia Pacific region. We want to use the head office logo as attached ( but don't have to be exactly the same, can be a variation to it) as a base and then add Asia Pacific alongside the logo.
We would prefer to have be bilingual Eng + Chinese, although we don't really have Chinese company name .

Industry/Entity Type

Business

Contact Information for Business Card

Clara Jo Tsang
 

VP,
APAC M&A Operations
Orin Vantage Asia Pacific Limited
 
Unit 1407, K18
18 Tai Lok Shan Road, 
Hong Kong 
 
M: +852 6038 1742
T : +852 2836 4100
F : +852 2836 4177
VOIP: 4158
 
cjtsang@orinvantage.com

Font styles to use
Serif
Sans Serif

Colors

Designer to choose colors to be used in the design.

Requirements
Must have
• APAC Office

```html
<!DOCTYPE html>
<html lang="en">
<head>
<meta charset="utf-8">
<title>Orin Vantage Business Card</title>
<link rel="stylesheet" href="https://fonts.googleapis.com/css2?family=Open+Sans:wght@400;600;700&family=Roboto:wght@300;400&display=swap">
<style>
  :root {
    --backdrop: #2b2b2c;
    --cyan: #1fadd3;
    --cyan-line: #22b3dc;
    --charcoal: #1d1e20;
    --navy: #0f2942;
    --white: #ffffff;
    --soft-white: #e9eef1;
  }
  html, body {
    margin: 0;
    padding: 0;
    width: 1200px;
    height: 960px;
    overflow: hidden;
    background: var(--backdrop);
  }
  .canvas {
    position: relative;
    width: 1200px;
    height: 960px;
  }
  .card {
    position: absolute;
    left: 320px;
    width: 600px;
    box-shadow: 0 4px 14px rgba(0,0,0,0.45);
  }

  /* Front face */
  .card-front {
    top: 108px;
    height: 338px;
    background: var(--cyan);
  }
  .front-name {
    position: absolute;
    left: 0;
    right: 0;
    top: 238px;
    margin: 0;
    text-align: center;
    font-family: "Open Sans", sans-serif;
    font-weight: 700;
    font-size: 40px;
    line-height: 48px;
    color: var(--soft-white);
    letter-spacing: 1px;
  }
  .front-web {
    position: absolute;
    left: 0;
    right: 0;
    top: 284px;
    text-align: center;
    font-family: "Roboto", sans-serif;
    font-weight: 300;
    font-size: 14px;
    letter-spacing: 6.5px;
    color: var(--soft-white);
  }

  /* Back face */
  .card-back {
    top: 492px;
    height: 343px;
    background: var(--charcoal);
    overflow: hidden;
  }
  .back-panel {
    position: absolute;
    inset: 0;
  }
  .holder-name {
    position: absolute;
    left: 35px;
    top: 25px;
    margin: 0;
    font-family: "Open Sans", sans-serif;
    font-weight: 600;
    font-size: 20px;
    line-height: 26px;
    color: var(--cyan);
    letter-spacing: -0.3px;
  }
  .holder-title {
    position: absolute;
    left: 36px;
    top: 51px;
    font-family: "Open Sans", sans-serif;
    font-weight: 600;
    font-size: 13px;
    color: var(--white);
  }
  .office-address {
    position: absolute;
    left: 35px;
    top: 126px;
    margin: 0;
    font-family: "Open Sans", sans-serif;
    font-style: normal;
    font-size: 14px;
    line-height: 18.8px;
    color: var(--soft-white);
  }
  .contact-list {
    position: absolute;
    left: 35px;
    top: 226px;
    margin: 0;
    padding: 0;
    list-style: none;
    font-family: "Open Sans", sans-serif;
    font-size: 14px;
    line-height: 19px;
    color: var(--soft-white);
  }
  .contact-list li {
    display: flex;
    align-items: center;
    gap: 8px;
  }
  .contact-list svg {
    width: 14px;
    height: 14px;
    fill: var(--cyan);
  }
  .voip {
    position: absolute;
    left: 35px;
    top: 292px;
    font-family: "Open Sans", sans-serif;
    font-size: 14px;
    color: var(--soft-white);
  }
  .brand-name {
    position: absolute;
    left: 300px;
    width: 290px;
    top: 154px;
    margin: 0;
    text-align: center;
    font-family: "Open Sans", sans-serif;
    font-weight: 700;
    font-size: 31px;
    line-height: 40px;
    color: var(--cyan);
  }
</style>
</head>
<body>
<main class="canvas">

  <section class="card card-front" aria-label="Card front">
    <p class="front-name">ORIN VANTAGE</p>
    <div class="front-web">www.orinvantage.com</div>
  </section>

  <section class="card card-back" aria-label="Card back">
    <svg class="back-panel" width="600" height="343" viewBox="0 0 600 343" aria-hidden="true">
      <polygon points="423,0 600,0 600,343 425,343 275,170" fill="var(--navy)"/>
      <polyline points="423,0 275,170 425,343" fill="none" stroke="var(--cyan-line)" stroke-width="2"/>
    </svg>

    <h1 class="holder-name">CLARA JO TSANG</h1>
    <div class="holder-title">VP</div>

    <address class="office-address">
      APAC M&amp;A Operations<br>
      Orin Vantage Asia Pacific Limited<br>
      Unit 1407, K18<br>
      18 Tai Lok Shan Road<br>
      Hong Kong
    </address>

    <ul class="contact-list">
      <li>
        <svg viewBox="0 0 24 24" aria-label="Telephone"><path d="M6.6 10.8a15.1 15.1 0 0 0 6.6 6.6l2.2-2.2c.3-.3.7-.4 1-.2 1.1.4 2.3.6 3.6.6.6 0 1 .4 1 1V20c0 .6-.4 1-1 1A17 17 0 0 1 3 4c0-.6.4-1 1-1h3.5c.6 0 1 .4 1 1 0 1.3.2 2.5.6 3.6.1.3 0 .7-.2 1z"/></svg>
        +852 2836 4100
      </li>
      <li>
        <svg viewBox="0 0 24 24" aria-label="Mobile"><path d="M7 1h10a2 2 0 0 1 2 2v18a2 2 0 0 1-2 2H7a2 2 0 0 1-2-2V3a2 2 0 0 1 2-2zm0 3v15h10V4zm5 16.2a1 1 0 1 0 0 .1z"/></svg>
        +852 6038 1742
      </li>
      <li>
        <svg viewBox="0 0 24 24" aria-label="Fax"><path d="M6 2h9l3 3v4H6zM3 10h18a1 1 0 0 1 1 1v8a1 1 0 0 1-1 1h-3v2H6v-2H3a1 1 0 0 1-1-1v-8a1 1 0 0 1 1-1zm5 6v4h8v-4z"/></svg>
        +852 2836 4177
      </li>
    </ul>

    <div class="voip">VOIP: 4158</div>

    <p class="brand-name">ORIN VANTAGE</p>
  </section>

</main>
</body>
</html>
```